Create a Brochure Design for Brantley Homecare

Brantley Homecare is a subsidiary of the Brantley Care Group. This brochure is specifically for the Brantley Homecare company and brand. Create a 3 panel, A4, front and back, tri-fold brochure. This brochure will be a way to introduce our Homecare services to the community, prospective clients, and various referral partners. The brochure must be eye catching, unique in its deliverables and demonstrate both attention to detail and comfort. Our organization is sophisticated and built around warmth, care and individualized personal attention. The most important aspect of this design is to focus on creating a nurturing, warm, and inviting feel where you would want to have a Nurse or Nurse’s Aide in your own home or a loved one’s home.

I am open to the creativity of the designer to develop something based on the above criteria; however I would like the design to work well with the existing collateral material. What I mean by that is that while I want everything to have its own personality and stand out as its own brand representative, I still need to be able to tell that the overall design concept stays stylistically inside of the same ‘family’ of existing designed material. Because of this, below I would like for the designer to pull inspiration from the link to our website (Located below) as well as from the attachment of our recently refreshed business cards (Attached). This should allow each design to be unique and creative, while still staying inside of a framework and the feel/style that I am looking for.

Finally, I want all the designers to understand that this brochure design is for a private, in home, healthcare company where we are responsible for providing personalized care for a culturally and ethnically diverse make-up clientele of all ages. The photos that are used must represent an image of warmth, care, and a positive interaction between client and caregiver.

Look under the Brantley Homecare tab at www.brantleycaregroup.example

Industry/Entity Type

Healthcare

Requirements
Must have
• • The Brantley Homecare company logo must be included.

```html
<!DOCTYPE html>
<html lang="en">
<head>
<meta charset="utf-8">
<title>Brantley Homecare – Tri-fold Brochure</title>
<link href="https://fonts.googleapis.com/css2?family=Source+Sans+3:ital,wght@0,400;0,600;0,700;1,400&display=swap" rel="stylesheet">
<style>
  :root{
    --teal:#1f6b63;
    --teal-dark:#15524c;
    --teal-light:#cfe6e1;
    --coral:#f07a6f;
    --coral-soft:#f6a49b;
    --blush:#f8d6d2;
    --maroon:#7a1f2e;
    --cover-green:#5f9a4e;
    --ink:#2a2a2a;
    --paper:#ffffff;
    --stage:#d9d9d9;
  }
  *{box-sizing:border-box;margin:0;padding:0}
  html,body{width:1200px;height:1106px;overflow:hidden}
  body{background:var(--stage);font-family:"Source Sans 3",Arial,sans-serif;color:var(--ink);position:relative}

  .spread{position:absolute;left:230px;width:740px;height:523px;background:var(--paper);
    display:grid;grid-template-columns:repeat(3,1fr);box-shadow:0 6px 18px rgba(0,0,0,.25);overflow:hidden}
  .spread--outside{top:20px}
  .spread--inside{top:563px}
  .panel{position:relative;overflow:hidden;font-size:8.6px;line-height:1.35}

  .brand{position:absolute;top:16px;right:12px;display:flex;align-items:center;gap:5px;
    font-weight:600;font-size:14px;color:var(--teal)}
  .brand__dot{width:10px;height:10px;border-radius:50%;background:var(--coral)}
  .topline{position:absolute;top:0;left:0;right:0;height:9px;background:var(--teal-light)}

  .photo{position:absolute}
  .wave{position:absolute;left:0;bottom:0;width:100%;height:70px}

  /* outside: panel 1 */
  .services{position:absolute;top:72px;left:0;right:0;height:113px;background:var(--teal);color:#fff;padding:12px 14px}
  .services p{margin-bottom:7px}
  .label{color:var(--coral);font-weight:700}
  .schedule{position:absolute;top:288px;left:0;right:0;height:172px;background:var(--teal);color:#fff;padding:10px 14px}
  .schedule h2{color:var(--coral);font-size:15px;font-weight:600;margin-bottom:3px}

  /* outside: panel 2 */
  .faq{position:absolute;left:14px;right:14px}
  .faq h3{font-size:9px;font-weight:700;margin-bottom:5px}
  .faq--one{top:50px}
  .faq--two{top:298px}
  .contact{position:absolute;top:372px;left:0;right:0;height:92px;background:var(--coral);color:#fff;text-align:center;padding:10px}
  .contact h2{font-size:14px;font-weight:600;margin-bottom:4px;letter-spacing:.5px}
  .contact p{font-size:7.4px;line-height:1.4}

  /* outside: cover */
  .cover__blush{position:absolute;top:0;left:0;width:92px;height:74px;background:var(--blush)}
  .cover .brand{font-size:17px;top:24px}
  .tagline{position:absolute;left:14px;right:10px;top:385px;color:#fff;font-style:italic;font-size:16px;line-height:1.25}
  .tagline span{display:block;padding-left:34px}

  /* inside */
  .about{background:var(--teal);color:#fff}
  .about__text{position:absolute;left:14px;right:14px}
  .about__text--top{top:14px}
  .about__text--bottom{top:300px}
  .promise{background:#fff}
  .promise__text{position:absolute;left:16px;right:14px;top:16px}
  .promise__text p{margin-bottom:7px}
  .promise h3{font-size:9px;font-weight:700;margin-bottom:2px}
  .promise ul{list-style:none}
  .care{background:var(--coral);color:#fff}
  .care .topline{background:var(--teal-light);height:9px}
  .care .brand{background:#fff;padding:3px 6px;top:14px;right:10px;font-size:12px}
  .care__text{position:absolute;left:14px;right:14px;top:54px}
  .care__text p{margin-bottom:8px}
  .care ul{list-style:none;margin-bottom:8px}
  .care .label{color:#fff}
</style>
</head>
<body>

<!-- OUTSIDE SPREAD -->
<section class="spread spread--outside">
  <div class="panel">
    <div class="topline"></div>
    <div class="brand"><span class="brand__dot"></span>Brantley</div>
    <div class="services">
      <p><span class="label">Medication Services</span> – Our licensed nurse will pre-pour your medication in weekly pill containers for a 28-day period.</p>
      <p><span class="label">Transportation Services</span> – Our Care Professionals run errands or escort you to the grocery store, your personal appointments (physician, beautician, therapy), or other outings.</p>
    </div>
    <div class="photo" role="img" aria-label="Photo of a caregiver with an elderly client" style="top:187px;left:0;width:96px;height:98px;background:linear-gradient(135deg,#c9b2a0,#7f6a5c)"></div>
    <div class="photo" role="img" aria-label="Portrait photo of a smiling caregiver" style="top:187px;left:100px;width:146px;height:98px;background:linear-gradient(135deg,#e9e2d8,#8d6a52)"></div>
    <div class="schedule">
      <h2>Your Schedule</h2>
      <p>Brantley Homecare is flexible with your care needs. As you need more or less care, your schedule can be adjusted to accommodate your needs. We have found that a set schedule works best (same days and times each week). This allows you to be able to depend on the same care professional(s) each week. You determine the schedule, from a minimum of four hours per shift to 24 hours of care per day, 7 days per week, 365 days per year. Our Scheduling department is available 24 hours per day.</p>
    </div>
    <svg class="wave" viewBox="0 0 247 70" preserveAspectRatio="none">
      <path d="M0 8 C70 40 160 40 247 6 L247 70 L0 70Z" fill="#fff"/>
      <path d="M0 20 C80 55 170 40 247 14 L247 70 L0 70Z" fill="var(--maroon)" opacity=".85"/>
      <path d="M0 34 C90 64 180 50 247 28 L247 70 L0 70Z" fill="var(--teal)"/>
    </svg>
  </div>

  <div class="panel">
    <div class="topline"></div>
    <div class="brand"><span class="brand__dot"></span>Brantley</div>
    <div class="faq faq--one">
      <h3>What makes Brantley Homecare different from other homecare agencies?</h3>
      <p>Answer: Brantley Homecare has earned a reputation in the community for providing compassionate, dependable, high-quality home care services. We employ Care Professionals who embody the Brantley vision of consistent, outstanding service for every client.</p>
    </div>
    <div class="photo" role="img" aria-label="Photo of a caregiver playing a game with an elderly client" style="top:187px;left:58px;width:104px;height:98px;background:linear-gradient(135deg,#b7b8b0,#5d5a52)"></div>
    <div class="photo" role="img" aria-label="Photo of a caregiver helping a client at home" style="top:187px;left:166px;width:81px;height:98px;background:linear-gradient(135deg,#9bb48a,#6a4f46)"></div>
    <div class="faq faq--two">
      <h3>Are your employees screened?</h3>
      <p>Answer: All of our Care Professionals are pre-screened and submit to a comprehensive testing and assessment process which includes their criminal and driving abstracts, as well as screenings through Child/Adult Protective Services.</p>
    </div>
    <div class="contact">
      <h2>CONTACT US</h2>
      <p>480 Harborview Ave, Suite 210, Honolulu, HI 96801<br>Phone (555) 014-2280<br>Fax (555) 014-2281<br>hello@brantleycare.example</p>
    </div>
    <svg class="wave" viewBox="0 0 247 70" preserveAspectRatio="none">
      <path d="M0 10 C90 45 170 40 247 12 L247 70 L0 70Z" fill="#fff"/>
      <path d="M0 26 C90 60 170 50 247 30 L247 70 L0 70Z" fill="var(--maroon)" opacity=".8"/>
      <path d="M0 40 C90 66 170 58 247 44 L247 70 L0 70Z" fill="var(--coral-soft)"/>
    </svg>
  </div>

  <div class="panel cover">
    <div class="cover__blush"></div>
    <div class="brand"><span class="brand__dot"></span>Brantley</div>
    <div class="photo" role="img" aria-label="Photo of a caregiver's hand holding an elderly client's hand" style="top:78px;left:0;right:0;height:392px;background:linear-gradient(160deg,#e8e4dc 0%,#c9a89a 35%,#7fa66d 70%,#4f8a43 100%)"></div>
    <p class="tagline">Some one you can depend<span>on without question......</span></p>
    <svg class="wave" viewBox="0 0 247 70" preserveAspectRatio="none">
      <path d="M0 0 L247 0 L247 70 L0 70Z" fill="var(--cover-green)"/>
      <path d="M0 30 C80 10 170 16 247 36 L247 70 L0 70Z" fill="var(--teal-dark)" opacity=".45"/>
    </svg>
  </div>
</section>

<!-- INSIDE SPREAD -->
<section class="spread spread--inside">
  <div class="panel about">
    <p class="about__text about__text--top">Brantley Homecare operates under the Brantley Care Group umbrella. With thousands of satisfied clients and now an exciting new alternative, Brantley Care Group continues to stay focused on what we do best: take care of those who need us. Headquartered in Honolulu, Hawaii, the Brantley Care Group's Administrative Offices are located at 480 Harborview Avenue, Suite 210. The Group serves the island community of Oahu.</p>
    <div class="photo" role="img" aria-label="Photo of a smiling caregiver with a 'We're here to help' message" style="top:128px;left:0;right:0;height:160px;background:linear-gradient(120deg,#b9c7cf,#e9e6e2 55%,#c8827a)"></div>
    <p class="about__text about__text--bottom">Dana Brantley, founder, president, and CEO of Brantley Care Group, discovered the need for dependable, compassionate home care at the tender age of 18, when she was seriously injured in an accident. Tragedy became inspiration, and in 1996, at the age of 21, she started Brantley Homecare.</p>
    <svg class="wave" viewBox="0 0 247 70" preserveAspectRatio="none">
      <path d="M0 14 C80 50 170 44 247 16 L247 70 L0 70Z" fill="#fff"/>
      <path d="M0 30 C90 62 180 50 247 30 L247 70 L0 70Z" fill="var(--teal-dark)"/>
    </svg>
  </div>

  <div class="panel promise">
    <div class="promise__text">
      <p>Since 1996, we have been serving the island community of Oahu with private duty home care. We provide in-home services ranging from light housekeeping to personal care and skilled nursing. We strive to give compassionate, dependable care of the highest quality while maintaining extremely competitive rates. Everything we do is geared toward meeting the individual needs of our clients.</p>
      <p>Whether you need a little help or a lot of help, you'll find that Brantley Homecare's services are a cut above the rest. The Brantley Way is special; it is compassionate, professional, dependable and flexible.</p>
      <h3>All of our Care Professionals:</h3>
      <ul>
        <li>Are bonded, insured, and supervised;</li>
        <li>Have passed both criminal and abuse background checks;</li>
        <li>Have been screened for TB;</li>
        <li>Are certified in CPR and First Aid</li>
      </ul>
    </div>
    <div class="photo" role="img" aria-label="Photo of a caregiver with a young client, captioned 'Quality home care services, The Brantley Way'" style="top:330px;left:0;right:0;height:130px;background:linear-gradient(120deg,#6f5a52,#d9b7b0 60%,#f0d9d6)"></div>
    <svg class="wave" viewBox="0 0 247 70" preserveAspectRatio="none">
      <path d="M0 10 C90 44 170 40 247 10 L247 70 L0 70Z" fill="#fff"/>
      <path d="M0 28 C90 60 180 52 247 30 L247 70 L0 70Z" fill="var(--coral-soft)" opacity=".7"/>
    </svg>
  </div>

  <div class="panel care">
    <div class="topline"></div>
    <div class="brand"><span class="brand__dot"></span>Brantley</div>
    <div class="care__text">
      <p>All client care is supervised by a licensed Registered Nurse whose duties include:</p>
      <ul>
        <li>Regular home visits</li>
        <li>Client evaluation</li>
        <li>Care Professional supervision</li>
        <li>Reviewing and updating client care plans</li>
        <li>24/7 phone support</li>
      </ul>
      <p>Brantley Homecare provides two different levels of care. Our Home Care Consultant will assist the client and family in determining the appropriate level of care needed during the complimentary initial consultation.</p>
      <p><span class="label">Personal Care</span> – We meet personal care needs, provide companionship, run errands, and do light housekeeping, along with assisting you with the activities of daily living.</p>
      <p><span class="label">Skilled Nursing Care</span> – We offer a wide range of skilled nursing services using RNs and LPNs who provide treatment from wound care to life support, in addition to all of the services performed by our Nurse Aides.</p>
    </div>
    <div class="photo" role="img" aria-label="Photo of caregivers sharing a warm moment with elderly clients" style="top:368px;left:10px;right:0;height:110px;background:linear-gradient(120deg,#9fb5c4,#d7c2b4 55%,#a0746a)"></div>
  </div>
</section>

</body>
</html>
```